Social Media Templates for Fieldhouse Raffle Fund

We need a set of Square (1080 x 1080) social media posts.

My company works with sports clubs, helping them to raise money with a lottery.

I need a set of social media image that I can use to appeal to new Fieldhouse Raffle Fund to encourage them to start a lottery with us.

This landing page has worked very well for us https://fieldhouserafflefund.com/fieldhouse-raffle-fund/

THING THAT APPEAL TO CLUBS

No Setup Fees/Start for Free - (We don’t charge any registration fees, or setup fees so you can start raising money from the first draw.)

Start Straight Away - (A club can start raising money straight away.)

Sustainable Income - (The average player plays for 7 years)

Subscription Lottery - (once a player joins, they play until the choose to leave. A club doesn't have to sell tickets every draw to the same people)

All Administration Taken Care Of - (We do all the hard work, so they can focus on running their club.)

Unlimited Income - (There is no limit on the amount of money a club can raise: the more players, the more funds for the club.)

Fundraising reach - (Reach new fans)

50% of the sales is guaranteed profit

£25,000 jackpot - (a person could win £25,000 every week)

Price - (It costs just £1 per week to enter)

Help Your Club - (100% of the profit goes to the club who a player chooses to support)

You can see all the clubs we work with on www.fieldhouserafflefund.com

The images will also be used on Chatterwall. You can see some examples here https://www.chatterwall.com/FieldhouseRaffleFund/ (you may need a proxy to view this page as it is only viewable in the UK, so I have attached some screenshots)

You can find the Fieldhouse Raffle Fund Logo here https://www.logovault.com/winwellgroup/

Target Market(s)

People who are involved with amateur sports in United Kingdom

Industry/Entity Type

Gambling

Font styles to use
Sans Serif

Requirements
Must have
• My project must look great on social social media and encourage people to get in touch about starting a lottery with us.

Adobe Suite files must be provided

```html
<!DOCTYPE html>
<html lang="en">
<head>
<meta charset="utf-8">
<title>Fieldhouse Raffle Fund – Social Post</title>
<link rel="stylesheet" href="https://fonts.googleapis.com/css2?family=Montserrat:wght@700;800;900&family=Raleway:wght@400;500&display=swap">
<style>
  :root {
    --grass-dark: #1f5a1c;
    --grass-mid: #2f7a27;
    --grass-light: #4c9a3a;
    --brand-blue: #2a7dc0;
    --brand-orange: #f26a12;
    --ink: #3d3d3d;
    --white: #ffffff;
    --page: #ece8e1;
  }
  * { margin: 0; padding: 0; box-sizing: border-box; }
  html, body { width: 1200px; height: 1200px; overflow: hidden; background: var(--page); }
  .post {
    position: relative;
    width: 1200px;
    height: 1200px;
    overflow: hidden;
    font-family: "Raleway", Arial, sans-serif;
    color: var(--ink);
  }
  .post-art { position: absolute; inset: 0; width: 1200px; height: 1200px; }
  .brand-panel {
    position: absolute;
    left: 100px; top: 80px; width: 300px; height: 240px;
    background: var(--brand-blue);
    display: flex; align-items: center; justify-content: center;
  }
  .brand-name {
    font-family: "Montserrat", Arial, sans-serif;
    font-weight: 800;
    font-size: 38px;
    line-height: 46px;
    color: var(--white);
    text-align: center;
  }
  .benefits { position: absolute; left: 52px; top: 351px; width: 480px; list-style: none; }
  .benefit {
    position: relative;
    padding-left: 22px;
    font-size: 17px;
    line-height: 22px;
    margin-bottom: 21px;
  }
  .benefit::before {
    content: "";
    position: absolute; left: 0; top: 6px;
    width: 9px; height: 9px; border-radius: 50%;
    background: var(--brand-orange);
  }
  .benefit-title { font-family: "Montserrat", Arial, sans-serif; font-weight: 800; color: var(--brand-blue); font-size: 16px; }
  .jackpot {
    position: absolute; left: 47px; top: 812px;
    font-family: "Montserrat", Arial, sans-serif; font-weight: 900;
    font-size: 54px; line-height: 60px; color: var(--brand-orange); letter-spacing: -0.5px;
  }
  .jackpot-note { position: absolute; left: 47px; top: 876px; font-size: 28px; line-height: 34px; font-weight: 400; }
  .reach-bar {
    position: absolute; left: 48px; top: 924px; width: 570px; height: 45px;
    background: var(--brand-blue); color: var(--white);
    font-size: 31px; line-height: 45px; padding-left: 8px; white-space: nowrap;
  }
  .profit-figure {
    position: absolute; left: 58px; top: 972px;
    font-family: "Montserrat", Arial, sans-serif; font-weight: 900;
    font-size: 100px; line-height: 110px; color: var(--brand-orange); letter-spacing: -5px;
  }
  .profit-text {
    position: absolute; left: 312px; top: 985px;
    font-family: "Montserrat", Arial, sans-serif; font-weight: 800;
    font-size: 32px; line-height: 43px; color: var(--brand-blue);
  }
  .fine-print { position: absolute; left: 67px; top: 1096px; width: 590px; font-size: 17px; line-height: 19px; }
  .fine-print p { margin-bottom: 14px; }
  .fine-print strong { font-family: "Montserrat", Arial, sans-serif; font-weight: 800; color: var(--brand-orange); font-size: 16px; }
  .partner-draw {
    position: absolute; left: 905px; top: 835px; width: 240px;
    font-family: "Montserrat", Arial, sans-serif; font-weight: 900;
    font-size: 40px; line-height: 42px; color: var(--white);
  }
  .partner-group {
    position: absolute; left: 915px; top: 1040px; width: 240px;
    font-family: "Montserrat", Arial, sans-serif; font-weight: 800;
    color: var(--white);
  }
  .partner-group .name { display: block; font-size: 54px; line-height: 58px; }
  .partner-group .tag { display: block; font-size: 18px; line-height: 22px; }
</style>
</head>
<body>
<main class="post">
  <svg class="post-art" viewBox="0 0 1244 1244" width="1200" height="1200">
    <defs>
      <linearGradient id="grassFill" x1="0" y1="0" x2="1" y2="1">
        <stop offset="0" stop-color="#2f7a27"/>
        <stop offset="0.5" stop-color="#3f8c32"/>
        <stop offset="1" stop-color="#1f5a1c"/>
      </linearGradient>
      <linearGradient id="trophyFill" x1="0" y1="0" x2="1" y2="1">
        <stop offset="0" stop-color="#f6d85a"/>
        <stop offset="1" stop-color="#b58a12"/>
      </linearGradient>
      <linearGradient id="teamPhotoFill" x1="0" y1="0" x2="0" y2="1">
        <stop offset="0" stop-color="#3f6b3a"/>
        <stop offset="0.25" stop-color="#d83a3a"/>
        <stop offset="0.7" stop-color="#e02a2a"/>
        <stop offset="1" stop-color="#4d7a52"/>
      </linearGradient>
      <clipPath id="designClip"><rect width="1244" height="1244"/></clipPath>
    </defs>
    <g clip-path="url(#designClip)">
      <rect class="grass" width="1244" height="1244" fill="url(#grassFill)" role="img" aria-label="Artificial grass pitch texture"/>
      <rect class="trophy" x="0" y="0" width="200" height="262" rx="20" fill="url(#trophyFill)" opacity="0.9" role="img" aria-label="Gold trophy cup"/>
      <circle class="panel-white" cx="294" cy="834" r="600" fill="var(--white)"/>
      <circle class="panel-edge" cx="294" cy="834" r="606" fill="none" stroke="var(--brand-orange)" stroke-width="3"/>
      <circle class="team-photo" cx="960" cy="400" r="391" fill="url(#teamPhotoFill)" role="img" aria-label="Youth football team in red kit huddled on the pitch"/>
      <circle class="team-photo-ring" cx="960" cy="400" r="362" fill="none" stroke="var(--white)" stroke-width="3"/>
    </g>
  </svg>

  <div class="brand-panel">
    <h1 class="brand-name">Fieldhouse<br>Raffle Fund</h1>
  </div>

  <ul class="benefits">
    <li class="benefit"><span class="benefit-title">No Setup Fees/Start for Free -</span><br>(We don’t charge any registration fees, or setup fees so you can start raising money from the first draw.)</li>
    <li class="benefit"><span class="benefit-title">Start Straight Away -</span> (A club can start raising money straight away.)</li>
    <li class="benefit"><span class="benefit-title">Sustainable Income -</span> (The average player plays for 7 years)</li>
    <li class="benefit"><span class="benefit-title">Subscription Lottery -</span> (once a player joins, they play until the choose to leave. A club doesn’t have to sell tickets every draw to the same people)</li>
    <li class="benefit"><span class="benefit-title">All Administration Taken Care Of -</span> (We do all the hard work, so they can focus on running their club.)</li>
    <li class="benefit"><span class="benefit-title">Unlimited Income -</span> (There is no limit on the amount of money a club can raise: the more players, the more funds for the club.)</li>
  </ul>

  <p class="jackpot">£25,000 JACKPOT</p>
  <p class="jackpot-note">(a person could win £25,000 every week)</p>
  <p class="reach-bar">Fundraising reach - (Reach new fans)</p>
  <p class="profit-figure">50%</p>
  <p class="profit-text">of the sales is<br>guaranteed profit</p>

  <div class="fine-print">
    <p><strong>Price -</strong> (It costs just £1 per week to enter)</p>
    <p><strong>Help Your Club -</strong> (100% of the profit goes to the club who a player chooses to support)</p>
  </div>

  <p class="partner-draw">The<br>Skyline<br>Draw</p>
  <p class="partner-group"><span class="name">winwell</span><span class="tag">GROUP SERVICES</span></p>
</main>
</body>
</html>
```